super clean and modern easy to read. Scandinavian type design.

Hi everyone, we need a wall menu for our retail space. We'd like something that goes along with the style of our website and is also editable (in case we change prices later on). The dimensions for the menu will be about 72 inches wide and about 48 inches high and it will be attached to the wall in our business. Please pull menu wording from this link: http://www.brivelounge.com/services

Feel free to shorten the descriptions.

The main sections of the menu are:
brive facials
enhancements
add-ons ($15, $20, and $30)
celebrity facials

Please include the picture of the woman on our homepage in the menu. I'll attach an image.

We would like to start with our process to simplify the steps we take.
1.)Complimentary skin analysis
2.) Choose your service
3.) Choose your products (recommendations are given)
4.) Enjoy!
5.) Further your results with take home products

Last little note, we can email you a larger Logo...Pixel Harbor would not let us upload the largest file that we have for the logo.

Target Market(s)

young, fun, hip, suburban women and men.

Industry/Entity Type

Retail

Font styles to use
Sans Serif

Requirements
Must have
• Not too much orange. Keep it clean and not too busy.
• the menu should make it super easy for someone to walk into the store and figure out the process.
• the 5 steps should be listed out first
• the 2 basic facials
• the add ons
• the enhancements (by price)
• the celebrity facials
• Advanced peels
• colors should be mainly blue and white (website) some orange used for framing categories or black. I like clean and not too busy. no cheesy.
Nice to have
• see colors on website. see style.
Should not have
• no clip art! no cursive formal writing.

```html
<!DOCTYPE html>
<html lang="en">
<head>
<meta charset="utf-8">
<title>brive lounge — service menu</title>
<link rel="stylesheet" href="https://fonts.googleapis.com/css2?family=Arimo:ital,wght@0,400;0,700;1,700&family=Roboto+Condensed:wght@400;500&display=swap">
<style>
:root{
  --teal:#5bc3d0;
  --teal-pale:#cdebf0;
  --orange:#ee8a24;
  --orange-light:#f7c79a;
  --ink:#1b1b1b;
  --grey:#444;
  --white:#fff;
}
*{margin:0;padding:0;box-sizing:border-box}
html,body{width:1200px;height:814px;overflow:hidden}
body{
  position:relative;
  font-family:"Arimo",Arial,sans-serif;
  color:var(--ink);
  background:linear-gradient(90deg,var(--teal-pale) 0,var(--white) 12%,var(--white) 80%,#c3e7ed 100%);
}
.abs{position:absolute}

/* process band */
.steps{position:absolute;left:0;top:0;width:1200px;height:136px;background:var(--teal)}
.step-num{
  position:absolute;top:40px;width:60px;height:60px;border-radius:50%;
  background:var(--orange);color:var(--white);
  font:500 40px/60px "Roboto Condensed",sans-serif;text-align:center;
}
.step-text{
  position:absolute;color:var(--white);
  font:500 29px/1.02 "Roboto Condensed",sans-serif;letter-spacing:-.3px;
}
.step-text small{font-size:13px;line-height:.9;display:inline-block;vertical-align:-1px}

/* section headings */
.heading{
  position:absolute;color:var(--teal);
  font:700 36px/1 "Arimo",sans-serif;letter-spacing:-.8px;white-space:nowrap;
  padding-bottom:6px;border-bottom:2px dashed var(--orange);
}
.heading .dots{display:inline-block;margin-left:6px;vertical-align:2px}
.heading .dots i{display:inline-block;width:21px;height:21px;border-radius:50%;background:var(--orange);margin-left:1px}

/* facial column */
.facials{left:48px;top:210px;width:250px;font-size:11.4px;line-height:14px}
.facial-title{font-weight:700;font-size:14.4px;line-height:18px;margin-bottom:2px}
.facials ul{list-style:none}
.facials li{padding-left:8px;text-indent:-8px}
.facials li::before,.list li::before{content:"• "}
.series{font-weight:700;font-size:12.8px;margin:3px 0 12px 8px}

/* lists */
.list{list-style:none;font-size:13.6px;line-height:18px}
.list li{padding-left:10px;text-indent:-10px}
.list li span{display:block;text-indent:0;color:var(--grey);line-height:16px}
.list b{font-weight:700}
.center-list li{margin-bottom:2.4px}
.right-list{font-size:13.2px;line-height:16.4px}

/* brand */
.brand-rule{position:absolute;left:346px;width:402px;height:2px;background:var(--teal)}
.brand{
  position:absolute;left:346px;top:422px;width:402px;text-align:center;
  color:var(--teal);font:700 64px/1 "Arimo",sans-serif;letter-spacing:-2.5px;white-space:nowrap;
}

/* bottom box */
.celebrity-box{position:absolute;left:52px;top:556px;width:718px;height:202px;border:3px solid var(--orange)}
.max-tab{
  position:absolute;left:2px;top:2px;width:288px;height:44px;
  background:linear-gradient(90deg,#9ad9e2,#e8f6f8);
  font:italic 700 28px/44px "Arimo",sans-serif;letter-spacing:-1px;padding-left:12px;white-space:nowrap;
}
.celebrity-box .heading{left:306px;top:12px;font-size:33px}
.stars{display:inline-block;margin-left:6px;vertical-align:1px}
.col{position:absolute;top:59px;font-size:9.6px;line-height:12.2px;color:var(--grey)}
.col h3{font-size:13.4px;line-height:15px;color:var(--ink);font-weight:700}
.col h3 em{font-style:normal;font-weight:400}
.divider{position:absolute;top:62px;width:2px;height:116px;background:var(--orange)}
</style>
</head>
<body>

<header class="steps">
  <div class="step-num" style="left:33px">1.</div>
  <div class="step-text" style="left:97px;top:44px">choose your<br>facial</div>
  <div class="step-num" style="left:246px">2.</div>
  <div class="step-text" style="left:311px;top:44px">complimentary<br>skin analysis</div>
  <div class="step-num" style="left:484px">3.</div>
  <div class="step-text" style="left:551px;top:34px;font-size:27px">choose<br>enhancement<br>products <small>(advice<br>given)</small></div>
  <div class="step-num" style="left:712px">4.</div>
  <div class="step-text" style="left:780px;top:44px">relax +<br>enjoy!</div>
  <div class="step-num" style="left:867px">5.</div>
  <div class="step-text" style="left:932px;top:44px">extend results with<br>take home products</div>
</header>

<!-- facials -->
<h2 class="heading" style="left:48px;top:160px">brive facials<span class="dots"><i></i><i></i></span></h2>
<section class="abs facials">
  <h3 class="facial-title">brive essential 30 min | $49</h3>
  <ul>
    <li>deep breathing with lavender essential oils</li>
    <li>includes In-depth skin analysis, with recommendations</li>
    <li>power cleanse x2, hot steam, exfoliation high frequency treatment or facial vacuum</li>
    <li>Shiatsu style massage</li>
    <li>lavender hot towel treatment</li>
    <li>customized mask, sun protection and lip treatment</li>
  </ul>
  <p class="series">Series of 3 $125</p>
  <h3 class="facial-title">brive essential 45 min | $69</h3>
  <ul>
    <li>facial customized specifically for your skins needs</li>
    <li>deep cleansing, exfoliation and hydration</li>
    <li>may include a bubbling pore mask, a pore vacuum, high frequency, special hydration mask</li>
    <li>lymphatic draining facial and neck massage</li>
    <li>hand, arm and décolleté massage</li>
  </ul>
  <p class="series" style="margin-bottom:0">Series of 3 $165</p>
</section>

<!-- arrows -->
<svg class="abs" style="left:310px;top:238px" width="120" height="98" viewBox="0 0 140 105" preserveAspectRatio="none" aria-hidden="true">
  <polygon points="0,22 70,22 84,34 14,34" fill="var(--orange-light)"/>
  <polygon points="70,0 84,12 138,62 124,52" fill="var(--orange-light)"/>
  <polygon points="14,34 84,34 84,12 138,62 84,105 84,82 14,82" fill="#f2a050"/>
  <polygon points="0,22 14,34 14,82 0,72" fill="var(--orange)"/>
</svg>
<svg class="abs" style="left:660px;top:244px" width="120" height="98" viewBox="0 0 140 105" preserveAspectRatio="none" aria-hidden="true">
  <polygon points="0,22 70,22 84,34 14,34" fill="var(--orange-light)"/>
  <polygon points="70,0 84,12 138,62 124,52" fill="var(--orange-light)"/>
  <polygon points="14,34 84,34 84,12 138,62 84,105 84,82 14,82" fill="#f2a050"/>
  <polygon points="0,22 14,34 14,82 0,72" fill="var(--orange)"/>
</svg>

<!-- enhancements -->
<h2 class="heading" style="left:389px;top:160px">enhancements $10<span class="dots"><i></i><i></i></span></h2>
<ul class="abs list center-list" style="left:444px;top:213px;width:300px">
  <li><b>vitamin c</b> (radiance + fine lines)</li>
  <li><b>peptide</b> (plump &amp; smooth)</li>
  <li><b>hyaluronic acid</b><span>(moisture.anti-aging)</span></li>
  <li><b>retinol</b> (fine lines.age spots)</li>
  <li><b>dehydrated eye treatment</b></li>
  <li><b>cherry enzyme peel</b><span>(antioxidant, healthy glow)</span></li>
  <li><b>pumpkin</b> (revitalizes, reduce lines)</li>
</ul>

<!-- brand -->
<div class="brand-rule" style="top:398px"></div>
<div class="brand">brive lounge</div>
<div class="brand-rule" style="top:532px"></div>

<!-- add-ons -->
<h2 class="heading" style="left:802px;top:160px">add-ons $15<span class="dots"><i></i><i></i></span></h2>
<ul class="abs list right-list" style="left:802px;top:208px;width:360px">
  <li><b>wax - brow, chin or lip</b> (touch up)</li>
  <li><b>magnetic mud mask</b><span>(nourish.mineral infusion)</span></li>
  <li><b>peppermint/eucalyptus scalp massage</b><span>(invigorating.stress reduction)</span></li>
  <li><b>beard Oil Treatment</b><span>(softens and protects)</span></li>
</ul>

<h2 class="heading" style="left:802px;top:346px">add-ons $20<span class="dots"><i></i><i></i></span></h2>
<ul class="abs list right-list" style="left:802px;top:392px;width:360px">
  <li style="margin-bottom:4px"><b>me time - 20 min extra massage</b>(relax.enjoy)</li>
  <li><b>hand rejuvenation peel or microderm</b><span>(exfoliating, antiaging)</span></li>
</ul>

<h2 class="heading" style="left:802px;top:464px">add-ons $30<span class="dots"><i></i><i></i></span></h2>
<ul class="abs list right-list" style="left:802px;top:510px;width:360px;line-height:16.2px">
  <li><b>crystal microdermabrasion for face and neck or declotte - 2 passes</b> (fine lines, smoothing)</li>
  <li><b>diamond microdermabrasion for face and neck or declotte - 2 passes</b> (fine lines, smoothing)</li>
  <li><b>led light therapy - 20 min</b> (red antiaging) (blue acne)</li>
  <li><b>decollete treatment</b><span>(peel or microderm) (anti-aging, fine lines)</span></li>
  <li><b>whole face wax</b> (except brows)</li>
  <li><b>hand treatment - peel + microderm</b><span>(double exfoliation for antiaging)</span></li>
  <li><b>facial hydration cocktail -1 pass of microderm + 7 advanced serums to fully hydrate your skin</b><span>(glow,renew)</span></li>
  <li><b>microcurrent eye, mouth, or chin</b> (non-surgical face lift)</li>
</ul>

<!-- celebrity facials -->
<section class="celebrity-box">
  <div class="max-tab">for maximum results...</div>
  <h2 class="heading">celebrity facials<svg class="stars" width="50" height="23" viewBox="0 0 52 24" aria-hidden="true"><polygon fill="var(--orange)" points="12,1 15,9 23,9 16.5,14 19,22 12,17 5,22 7.5,14 1,9 9,9"/><polygon fill="var(--orange)" points="38,1 41,9 49,9 42.5,14 45,22 38,17 31,22 33.5,14 27,9 35,9"/></svg></h2>

  <div class="col" style="left:24px;width:118px">
    <h3>oxygen facial<br>50 min | $130<br><em>(marisol vane’s secret to red carpet skin)</em></h3>
    Rehydrates and plumps skin in less than an hour. naturally binds moisture within the skin for an instant glow.
  </div>
  <div class="divider" style="left:152px"></div>
  <div class="col" style="left:167px;width:136px">
    <h3>led therapy facial<br>50 min | $130<br><em>(nadia coren’s fav)</em></h3>
    We use LED for anti-aging, correcting discoloration, healing acne, and reversing the effects of sun damage. LED has been FDA approved for beauty treatments.
  </div>
  <div class="divider" style="left:308px"></div>
  <div class="col" style="left:323px;width:156px">
    <h3>Kavera Non Surgical Facelift| 50 min | $130<br><em>(Elena Draper)</em></h3>
    non-surgical facelift<br>first time client $99<br>only sold in series (depends on age and condition of skin) series of 3 $ series of 6 $ series of 10 $
  </div>
  <div class="divider" style="left:487px"></div>
  <div class="col" style="left:504px;width:200px">
    <h3>50 min | micro + peel | $130</h3>
    decrease fine lines &amp; wrinkles, reverses sun damage reduces scarring, rough texture, discoloration
    <h3 style="margin-top:12px">50 min Advanced Peel | $130</h3>
    Advanced peels reverse sun damage, wrinkles, acne, signs of aging
  </div>
</section>

</body>
</html>
```